RM Tomás Ledesma (Business Card)

Hi designers, in this work, I'm looking for an sophisticated stylish, elegant and proffesional personal card. We have a laboratory of pathology automated, with equipments high quality.
In this web the designers, have created my business logo, the name is "RM Tomás Ledesma"
In our lab, we principal work is to prepare the biopsies for further diagnostic of diseases like cancer, tumors, etc.
I need that the first face, only having my complete logo (Rm Tomás Ledesma, Laboratorio de procesamiento Histologico)
The overleaf, could repeat the same logo, like water logo.
In this face, I need to say: My full data:

Técnico en Anatomía Patológica
Tomás Ledesma Urquiza M.P 48213
Av. Duarte Quirós 817 - 2do piso - Instituto Brandsen.
Córdoba, Argentina
(0351) 158246093
ledesma.tomas@correoviva.com.ar

with respect the colors of card, use your imagination, the original logo color is violet, I haven't chosen a color base for the card.

attached pictures are examples of cards I like your DESIGN.
Attached too, the original logo to my company.

the size of card are:
horizontal: 9cm
vertical: 5,5cm

any question that you have, not doubt to question me,
Hand to work!

Industry/Entity Type

Laboratory

Requirements
Must have
• designers sophisticated, not simples, like show the images attached

```html
<!DOCTYPE html>
<html lang="es">
<head>
<meta charset="utf-8">
<title>Tomás Ledesma – Tarjeta personal</title>
<link rel="stylesheet" href="https://fonts.googleapis.com/css2?family=Arimo:wght@700&family=Open+Sans:wght@400&family=PT+Sans+Narrow&family=Raleway:wght@300&display=swap">
<style>
  :root {
    --backdrop: #2b2b2d;
    --card-white: #f3f3f3;
    --ink: #333333;
    --ink-soft: #3f3f3f;
    --grey: #8c8c8c;
    --violet: #7a2f9a;
    --violet-card: #5e2a82;
    --violet-card-light: #6d3393;
    --on-violet: #f1ecf4;
  }
  * { margin: 0; padding: 0; box-sizing: border-box; }
  html, body { width: 1200px; height: 900px; overflow: hidden; }
  body { background: var(--backdrop); position: relative; font-family: "Open Sans", sans-serif; }

  .card {
    position: absolute; left: 371px; width: 455px; height: 278px;
    border-radius: 14px; overflow: hidden;
  }
  .card-front { top: 161px; background: var(--card-white); }
  .card-back {
    top: 471px;
    background: linear-gradient(180deg, var(--violet-card-light), var(--violet-card));
  }

  /* front */
  .brand-mark {
    position: absolute; left: 40px; top: 122px; width: 150px;
    display: flex; align-items: center; gap: 7px;
    color: var(--violet); font-family: "Open Sans", sans-serif; font-size: 13px;
  }
  .brand-square { width: 12px; height: 12px; background: var(--violet); flex: none; }
  .divider { position: absolute; left: 206px; top: 63px; width: 1px; height: 154px; background: var(--grey); }
  .details { position: absolute; left: 234px; top: 59px; color: var(--ink-soft); }
  .person-name { font-family: "Arimo", sans-serif; font-weight: 700; font-size: 15.5px; color: var(--ink); }
  .licence { font-size: 11px; color: var(--violet); margin-top: 1px; }
  .role-lines { margin-top: 23px; font-size: 11px; line-height: 15px; }
  .contact-list { list-style: none; margin-top: 13px; font-size: 11.5px; line-height: 15.5px; }
  .contact-list li { display: flex; align-items: center; gap: 11px; }
  .contact-list svg { width: 10px; height: 10px; fill: var(--violet); flex: none; }
  .band { position: absolute; top: 264px; height: 14px; }
  .band-grey { left: 0; width: 205px; background: var(--grey); }
  .band-violet { left: 208px; right: 0; background: var(--violet); }

  /* back */
  .back-square {
    position: absolute; left: 217px; top: 112px; width: 22px; height: 22px;
    background: var(--on-violet);
  }
  .back-name {
    position: absolute; left: 78px; width: 296px; top: 164px; text-align: center;
    font-family: "Raleway", sans-serif; font-weight: 300; font-size: 16px;
    letter-spacing: 4px; color: var(--on-violet);
  }
  .back-rule { position: absolute; left: 78px; top: 191px; width: 296px; height: 1px; background: var(--on-violet); }
  .back-tagline {
    position: absolute; left: 0; right: 0; top: 196px; text-align: center;
    font-family: "PT Sans Narrow", sans-serif; font-size: 21px; color: var(--on-violet);
  }
</style>
</head>
<body>
  <section class="card card-front">
    <div class="brand-mark"><span class="brand-square"></span><span>Rm Tomás Ledesma</span></div>
    <div class="divider"></div>
    <div class="details">
      <p class="person-name">Tomás Ledesma Urquiza</p>
      <p class="licence">M.P. 48213</p>
      <div class="role-lines">
        <p>Técnico en Anatomía Patológica</p>
        <p>Av. Duarte Quirós 817 - 2do piso</p>
        <p>Instituto Brandsen, Córdoba, Argentina</p>
      </div>
      <ul class="contact-list">
        <li><svg viewBox="0 0 10 10"><path d="M2 0.5 L3.6 2.6 L2.7 3.6 Q3.8 6 6.3 7.3 L7.4 6.4 L9.5 8 L8.3 9.5 Q3.5 9 0.5 1.7 Z"/></svg>(0351) 158246093</li>
        <li><svg viewBox="0 0 10 10"><path d="M0.5 3.5 L5 0.8 L9.5 3.5 V9.2 H0.5 Z M1.5 4 L5 6.3 L8.5 4 L5 1.9 Z"/></svg>ledesma.tomas@correoviva.com.ar</li>
        <li><svg viewBox="0 0 10 10"><circle cx="5" cy="5" r="4.6"/><path d="M0.6 5 H9.4 M5 0.4 V9.6 M5 0.4 Q2.2 5 5 9.6 M5 0.4 Q7.8 5 5 9.6" stroke="#f3f3f3" stroke-width="0.7" fill="none"/></svg>www.tomas-ledesma.com.ar</li>
      </ul>
    </div>
    <div class="band band-grey"></div>
    <div class="band band-violet"></div>
  </section>

  <section class="card card-back">
    <div class="back-square"></div>
    <p class="back-name">RM TOMÁS LEDESMA</p>
    <div class="back-rule"></div>
    <p class="back-tagline">LABORATORIO DE PROCESAMIENTO HISTOLOGICO</p>
  </section>
</body>
</html>
```